Fresh, modern, fun business card for pediatric dental practice

Need a business card for fresh, modern, fun pediatric dental practice

Clean look that matches our website's font and colors

We prefer the look of curved corners on business cards

Target Market(s)

parents (mothers) of young children, professionals, mid-high class

Industry/Entity Type

Dental

Contact Information for Business Card

Maplebrook Pediatric Dentistry
482 Quarry Lane
Suite 517
Alderwick, PA 17990
717.555.0193
www.maplebrookkidsdental.example

Mei-Ran Tsai, DMD
Corinne Walbeck, DMD
(we are working on our email address, but we would like that on the card as well)

Font styles to use
Sans Serif

Requirements
Must have
• All info; we would also like to make cards for individual staff members
• colors from our website and color palatte, attatched
• use same font and design as website for branding
Nice to have
• clean, simple card that has a pop of color
• we would like to see a few designs with our tag line "where smiles get brighter"
• we are not sure if we want to have it on there or not
• we would like to see a few designs incorporating the ribbon graphic on our website where the word WELCOME is

```html
<!DOCTYPE html>
<html lang="en">
<head>
<meta charset="utf-8">
<title>Maplebrook Pediatric Dentistry – Business Card</title>
<link href="https://fonts.googleapis.com/css2?family=Questrial&display=swap" rel="stylesheet">
<style>
  :root {
    --plum: #5b2152;
    --plum-deep: #4a1a43;
    --gold: #f6b624;
    --magenta: #d42e92;
    --ink: #3a3a3a;
    --rule: #c9c9c9;
    --paper: #ffffff;
    --backdrop: #2b2b2b;
  }
  * { box-sizing: border-box; margin: 0; padding: 0; }
  html, body { width: 1200px; height: 900px; overflow: hidden; }
  body {
    background: var(--backdrop);
    font-family: "Questrial", "Century Gothic", sans-serif;
    position: relative;
  }
  .card {
    position: absolute;
    left: 330px;
    width: 540px;
    height: 309px;
    border-radius: 22px;
    overflow: hidden;
  }
  .card--front { top: 105px; background: var(--plum); }
  .card--back { top: 486px; background: var(--paper); }

  .brand-name {
    color: var(--gold);
    font-weight: 400;
    line-height: 1.05;
    text-transform: lowercase;
  }
  .card--front .brand {
    position: absolute;
    left: 0; right: 0; top: 92px;
    text-align: center;
  }
  .card--front .brand-name { font-size: 44px; letter-spacing: 1px; }
  .card--front .brand-sub { font-size: 30px; letter-spacing: 3px; }
  .brand-dot {
    display: inline-block;
    width: 22px; height: 22px;
    border-radius: 50%;
    background: var(--gold);
    margin-bottom: 10px;
  }
  .card--front .web {
    position: absolute;
    left: 0; right: 0; bottom: 42px;
    text-align: center;
    font-size: 13px;
    color: var(--gold);
    letter-spacing: 0.3px;
  }

  .card--back .brand {
    position: absolute;
    left: 28px; top: 98px;
    width: 200px;
    text-align: center;
  }
  .card--back .brand-name { font-size: 28px; }
  .card--back .brand-sub { font-size: 19px; letter-spacing: 1.5px; }
  .card--back .brand-dot { width: 16px; height: 16px; margin-bottom: 8px; }

  .divider {
    position: absolute;
    left: 248px; top: 60px;
    width: 1px; height: 150px;
    background: var(--rule);
  }
  .contact {
    position: absolute;
    left: 266px; top: 54px;
    color: var(--ink);
  }
  .contact .person {
    color: var(--magenta);
    font-size: 22px;
    margin-bottom: 6px;
  }
  .contact .address { font-size: 12.5px; line-height: 1.4; margin-bottom: 12px; }
  .contact .lines { list-style: none; font-size: 12.5px; line-height: 1.55; }
  .contact .lines li { display: flex; align-items: center; gap: 8px; }
  .contact .lines svg { width: 11px; height: 11px; flex: none; }
  .contact .accent { color: var(--magenta); }

  .wave { position: absolute; left: 0; bottom: 0; width: 540px; height: 130px; }
</style>
</head>
<body>

<section class="card card--front" aria-label="Card front">
  <div class="brand">
    <span class="brand-dot"></span>
    <div class="brand-name">maplebrook</div>
    <div class="brand-name brand-sub">pediatric dentistry</div>
  </div>
  <p class="web">www.maplebrookkidsdental.example</p>
</section>

<section class="card card--back" aria-label="Card back">
  <div class="brand">
    <span class="brand-dot"></span>
    <div class="brand-name">maplebrook</div>
    <div class="brand-name brand-sub">pediatric dentistry</div>
  </div>

  <div class="divider"></div>

  <div class="contact">
    <p class="person">Mei-Ran Tsai, DMD</p>
    <p class="address">Maplebrook Pediatric Dentistry<br>482 Quarry Lane<br>Suite 517, Alderwick, PA 17990</p>
    <ul class="lines">
      <li>
        <svg viewBox="0 0 12 12"><path d="M2.5 1 L4.5 1 L5.3 3.6 L4 4.6 C4.7 6 5.9 7.3 7.4 8 L8.4 6.7 L11 7.5 L11 9.5 C11 10.3 10.3 11 9.5 11 C5 11 1 7 1 2.5 C1 1.7 1.7 1 2.5 1 Z" fill="var(--magenta)"/></svg>
        717.555.0193
      </li>
      <li>
        <svg viewBox="0 0 12 12"><rect x="1" y="2.5" width="10" height="7" rx="1" fill="none" stroke="var(--magenta)" stroke-width="1.2"/><path d="M1.3 3 L6 6.6 L10.7 3" fill="none" stroke="var(--magenta)" stroke-width="1.2"/></svg>
        info@maplebrookkidsdental.example
      </li>
      <li>
        <svg viewBox="0 0 12 12"><circle cx="6" cy="6" r="4.8" fill="none" stroke="var(--magenta)" stroke-width="1.1"/><ellipse cx="6" cy="6" rx="2" ry="4.8" fill="none" stroke="var(--magenta)" stroke-width="1"/><path d="M1.2 6 H10.8" stroke="var(--magenta)" stroke-width="1"/></svg>
        <span>www.<span class="accent">maplebrookkidsdental</span>.example</span>
      </li>
    </ul>
  </div>

  <svg class="wave" viewBox="0 0 540 130" preserveAspectRatio="none" aria-hidden="true">
    <path d="M0 118 C120 40 250 70 360 80 C450 88 510 60 540 22 L540 130 L0 130 Z" fill="var(--gold)"/>
    <path d="M0 130 L0 126 C130 58 260 84 370 90 C455 95 515 68 540 36 L540 130 Z" fill="var(--plum)"/>
  </svg>
</section>

</body>
</html>
```